Pelican HVAC WordPress website design

Design a new modern, clean, website for HVAC mechanical business that uses company logo/colors for branding and recognition. Files attached are just for band and color information. Here is a website design that appeals to me https://www.corvellsupply.example/

A clear description of who we are and what we do

An easily-navigated site map

An easily-navigated site map for mobile devices

Easy-to-find contact information

Obvious call to action for service, installs or to schedule estimates

about us page

Provide a way for potential customers to contact us via text or email

provide a way that allows a customer to upload a picture to request a service call or quote.
Updates

I'm looking for the design to be completed in WordPress

Industry/Entity Type

HVAC Mechanical & Building Automation / Controls contractor

Coding

Coded - Design and coding required

Number of Pages Required

5+ page

Colors
0054AA
0677BA
7BADD7
CADEEF
E8F1F8

Requirements
Must have
• Design a new modern, clean, website for HVAC mechanical business that uses company logo/colors for branding and recognition. Files attached are just for band and color information. Here is a website design that appeals to me https://www.corvellsupply.example/ A clear description of who we are and what we do An easily-navigated site map An easily-navigated site map for mobile devices Easy-to-find contact information Obvious call to action for service, installs or to schedule estimates about us page Provide a way for potential customers to contact us via text or email provide a way that allows a customer to upload a picture to request a service call or quote.
Nice to have

```html
<!DOCTYPE html>
<html lang="en">
<head>
<meta charset="utf-8">
<title>Pelican HVAC</title>
<link href="https://fonts.googleapis.com/css2?family=Montserrat:wght@400;500;600;700&display=swap" rel="stylesheet">
<style>
:root{
  --blue-deep:#0054aa;
  --blue:#0677ba;
  --blue-mid:#7badd7;
  --blue-pale:#cadeef;
  --blue-mist:#e8f1f8;
  --ink:#2b2b2b;
  --grey-text:#8a8a8a;
  --panel:#ececec;
  --dark:#2c2c2c;
  --white:#ffffff;
}
*{box-sizing:border-box;margin:0;padding:0}
html,body{width:1200px;height:3516px;overflow:hidden}
body{position:relative;background:var(--white);font-family:"Montserrat",sans-serif;color:var(--ink)}
.abs{position:absolute}

/* header */
.brand{left:120px;top:10px;width:120px;height:96px;display:flex;align-items:center;gap:8px}
.brand-dot{width:18px;height:18px;border-radius:50%;background:var(--blue-deep);flex:none}
.brand-name{font-weight:700;font-size:20px;color:var(--blue-deep);line-height:1.05}
.btn-estimate{left:360px;top:14px;width:220px;height:46px;background:var(--blue);color:var(--white);border-radius:6px;font-size:13px;font-weight:600;display:flex;align-items:center;justify-content:center;gap:10px;letter-spacing:.5px}
.contact{top:10px;display:flex;align-items:center;gap:12px}
.contact-icon{width:40px;height:40px;border:2px solid var(--blue);border-radius:8px;display:flex;align-items:center;justify-content:center}
.contact-label{font-size:15px;font-weight:600;color:var(--blue);letter-spacing:.5px}
.contact-value{font-size:13px;color:var(--ink);margin-top:4px}
.nav-bar{left:420px;top:68px;width:780px;height:40px;background:var(--blue);display:flex;align-items:center;padding-left:40px;gap:0}
.nav-bar a{color:var(--white);text-decoration:none;font-size:14px;font-weight:600;padding:0 16px;border-right:1px solid rgba(255,255,255,.7);line-height:14px}
.nav-bar a:last-child{border-right:none}

/* hero */
.hero{left:0;top:120px;width:1200px;height:610px;background:linear-gradient(180deg,#5c6064 0%,#3d4044 55%,#2e3033 100%)}
.hero-photo{position:absolute;inset:0;background:radial-gradient(ellipse at 18% 40%,rgba(200,205,210,.35),transparent 45%),radial-gradient(ellipse at 85% 30%,rgba(170,175,180,.3),transparent 40%)}
.hero-title{left:0;top:262px;width:1200px;text-align:center;color:var(--white);font-weight:600;font-size:42px;line-height:54px;letter-spacing:1px}
.btn{background:var(--blue);color:var(--white);font-weight:600;font-size:13px;border-radius:8px;display:flex;align-items:center;justify-content:center;gap:8px;letter-spacing:.5px}
.hero-btn{left:492px;top:412px;width:216px;height:46px}
.hero-curve{left:0;top:560px;width:1200px;height:190px}

/* headings */
.section-title{left:0;width:1200px;text-align:center;font-size:46px;font-weight:600;color:var(--blue-deep);letter-spacing:1px}
.section-rule{left:570px;width:60px;height:3px;background:var(--blue-deep)}

/* who we are */
.who-photo{left:118px;top:898px;width:450px;height:460px;border-radius:50%;border:12px solid var(--blue);background:linear-gradient(160deg,#d9e6ee 0%,#a9bfcf 45%,#6b7f8f 100%)}
.who-kicker{left:582px;top:918px;font-size:34px;color:var(--blue-deep);font-weight:500;letter-spacing:1px}
.who-name{left:582px;top:958px;font-size:46px;color:var(--blue-deep);font-weight:500;letter-spacing:2px}
.who-copy{left:582px;top:1030px;width:510px;font-size:14px;line-height:22px;color:var(--grey-text)}
.who-copy p+p{margin-top:14px}
.who-btn{left:582px;top:1228px;width:216px;height:44px}

/* services */
.services{left:0;top:1400px;width:1200px;height:566px;background:linear-gradient(180deg,#ebebeb,#dedede)}
.services-photo{position:absolute;inset:0;background:radial-gradient(ellipse at 22% 45%,rgba(150,150,150,.35),transparent 35%),radial-gradient(ellipse at 80% 45%,rgba(150,150,150,.3),transparent 35%)}
.service-card{top:1592px;width:242px;height:268px;box-shadow:0 4px 10px rgba(0,0,0,.2)}
.service-card.is-active{top:1584px;height:284px}
.service-photo{height:160px;background:linear-gradient(160deg,#c9d3da,#7d8c98 60%,#4a5560)}
.service-panel{position:absolute;left:0;right:0;bottom:0;top:160px;background:var(--blue-deep);color:var(--white);text-align:center;padding-top:26px;font-size:20px;font-weight:500}
.service-go{width:34px;height:34px;border-radius:50%;background:var(--white);margin:18px auto 0;display:flex;align-items:center;justify-content:center}
.carousel-arrow{top:1700px;width:64px;height:64px;border-radius:50%;background:var(--white);border:3px solid #111;display:flex;align-items:center;justify-content:center}

/* about */
.about-card{top:2140px;width:468px;height:282px;background:var(--white);box-shadow:0 2px 12px rgba(0,0,0,.18);padding:28px 24px}
.about-card h3{font-size:26px;line-height:34px;font-weight:500;color:var(--blue-deep)}
.about-card p{margin-top:18px;font-size:14px;line-height:20px;color:var(--grey-text)}
.about-badge{left:548px;top:2232px;width:104px;height:104px;border-radius:50%;background:var(--blue-deep);border:4px solid var(--white);box-shadow:0 2px 8px rgba(0,0,0,.3);display:flex;align-items:center;justify-content:center;color:var(--white);font-size:14px;font-weight:700;text-align:center;line-height:16px}
.about-btn{left:492px;top:2462px;width:216px;height:44px}

/* request */
.request{left:0;top:2604px;width:1200px;height:660px;background:linear-gradient(180deg,#3a3a3a,#232323)}
.request-photo{position:absolute;inset:0;background:radial-gradient(ellipse at 50% 35%,rgba(110,110,110,.35),transparent 55%)}
.request-title{left:0;top:2680px;width:1200px;text-align:center;color:var(--white);font-size:46px;font-weight:500;letter-spacing:1px}
.request-rule{left:560px;top:2750px;width:80px;height:3px;background:var(--white)}
.field{left:244px;width:716px;height:44px;border:1.5px solid var(--white);color:var(--white);font-size:14px;font-weight:600;display:flex;align-items:center;padding-left:16px}
.field-upload{justify-content:space-between;padding-right:16px}
.field-message{height:98px;align-items:flex-start;padding-top:12px}
.submit{left:244px;top:3142px;width:716px;height:48px;border-radius:8px}

/* footer */
.footer-brand{left:110px;top:3336px;display:flex;align-items:center;gap:10px}
.footer-brand .brand-name{font-size:26px}
.footer-nav{left:632px;top:3370px;height:44px;border-left:4px solid var(--blue-deep);display:flex;align-items:center;padding-left:18px;gap:40px;font-size:16px;font-weight:500;color:var(--ink)}
.footer-rule{left:110px;top:3446px;width:980px;height:1px;background:#bbb}
.copyright{left:280px;top:3480px;font-size:13px;color:var(--ink)}
.legal{left:572px;top:3480px;font-size:13px;display:flex;gap:14px;color:var(--ink)}
</style>
</head>
<body>

<header>
  <div class="abs brand"><span class="brand-dot"></span><span class="brand-name">Pelican HVAC</span></div>
  <div class="abs btn-estimate">SCHEDULE ESTIMATES
    <svg width="16" height="16" viewBox="0 0 16 16"><circle cx="8" cy="8" r="7" fill="none" stroke="#fff" stroke-width="1.6"/><path d="M6.5 4.5 10 8l-3.5 3.5" fill="none" stroke="#fff" stroke-width="1.6"/></svg>
  </div>
  <div class="abs contact" style="left:604px">
    <div class="contact-icon"><svg width="22" height="16" viewBox="0 0 22 16"><rect x="1" y="1" width="20" height="14" rx="1.5" fill="none" stroke="#0677ba" stroke-width="2"/><path d="M1 2l10 7 10-7" fill="none" stroke="#0677ba" stroke-width="2"/></svg></div>
    <div><div class="contact-label">MAIL US TODAY !</div><div class="contact-value">info@pelicanhvac.example</div></div>
  </div>
  <div class="abs contact" style="left:884px">
    <div class="contact-icon" style="border-radius:50%"><svg width="20" height="20" viewBox="0 0 24 24"><path d="M6.6 10.8a15 15 0 0 0 6.6 6.6l2.2-2.2a1 1 0 0 1 1-.25 11.4 11.4 0 0 0 3.6.57 1 1 0 0 1 1 1V20a1 1 0 0 1-1 1A17 17 0 0 1 3 4a1 1 0 0 1 1-1h3.5a1 1 0 0 1 1 1c0 1.25.2 2.45.57 3.57a1 1 0 0 1-.25 1z" fill="#0677ba"/></svg></div>
    <div><div class="contact-label">CALL US TODAY !</div><div class="contact-value">555-014-2290</div></div>
  </div>
  <nav class="abs nav-bar"><a>HOME</a><a>ABOUT</a><a>SERVICES</a><a>CONTACT US</a></nav>
</header>

<section>
  <div class="abs hero" role="img" aria-label="Commercial rooftop air conditioning units under a dark overlay"><div class="hero-photo"></div></div>
  <h1 class="abs hero-title">ONE CALL FOR ALL YOUR<br>COMMERCIAL/ INDUSTRIAL NEED</h1>
  <div class="abs btn hero-btn">GET STARTED
    <svg width="16" height="16" viewBox="0 0 16 16"><circle cx="8" cy="8" r="7" fill="none" stroke="#fff" stroke-width="1.6"/><path d="M6.5 4.5 10 8l-3.5 3.5" fill="none" stroke="#fff" stroke-width="1.6"/></svg>
  </div>
  <svg class="abs hero-curve" viewBox="0 0 1200 190" preserveAspectRatio="none">
    <path d="M0 40 Q600 200 1200 40 L1200 190 L0 190 Z" fill="#fff"/>
    <path d="M80 70 Q600 200 1120 70" fill="none" stroke="#0054aa" stroke-width="10"/>
    <path d="M0 40 Q600 175 1200 40" fill="none" stroke="#0677ba" stroke-width="4"/>
  </svg>
</section>

<section>
  <h2 class="abs section-title" style="top:792px">WHO WE ARE</h2>
  <div class="abs section-rule" style="top:858px"></div>
  <div class="abs who-photo" role="img" aria-label="Technician servicing an outdoor air conditioning unit"></div>
  <div class="abs who-kicker">WELCOME TO</div>
  <div class="abs who-name">PELICAN HVAC</div>
  <div class="abs who-copy">
    <p>Lorem ipsum dolor sit amet, consectetur adipiscing elit, sed do eiusmod tempor incididunt ut labore et dolore magna aliqua. Quis ipsum suspendisse ultrices gravida. Risus commodo viverra maecenas accumsan lacus vel facilisis.</p>
    <p>Lorem ipsum dolor sit amet, consectetur adipiscing elit, sed do eiusmod tempor incididunt ut labore et dolore magna aliqua. Quis ipsum suspendisse ultrices gravida.</p>
  </div>
  <div class="abs btn who-btn">READ MORE
    <svg width="16" height="16" viewBox="0 0 16 16"><circle cx="8" cy="8" r="7" fill="none" stroke="#fff" stroke-width="1.6"/><path d="M6.5 4.5 10 8l-3.5 3.5" fill="none" stroke="#fff" stroke-width="1.6"/></svg>
  </div>
</section>

<section>
  <div class="abs services" role="img" aria-label="Faded photo of HVAC technicians at work"><div class="services-photo"></div></div>
  <h2 class="abs section-title" style="top:1474px">OUR SERVICES</h2>
  <div class="abs section-rule" style="top:1540px"></div>
  <div class="abs carousel-arrow" style="left:108px"><svg width="22" height="22" viewBox="0 0 22 22"><path d="M14 3 6 11l8 8" fill="none" stroke="#111" stroke-width="3"/></svg></div>
  <div class="abs carousel-arrow" style="left:1026px"><svg width="22" height="22" viewBox="0 0 22 22"><path d="M8 3l8 8-8 8" fill="none" stroke="#111" stroke-width="3"/></svg></div>

  <div class="abs service-card" style="left:198px">
    <div class="service-photo" role="img" aria-label="Technician checking an air conditioning unit"></div>
    <div class="service-panel">Lorem ipsum dolor<div class="service-go"><svg width="18" height="14" viewBox="0 0 18 14"><path d="M1 7h14M10 2l5 5-5 5" fill="none" stroke="#111" stroke-width="2"/></svg></div></div>
  </div>
  <div class="abs service-card is-active" style="left:478px">
    <div class="service-photo" role="img" aria-label="Technician repairing HVAC equipment"></div>
    <div class="service-panel">Lorem ipsum dolor<div class="service-go"><svg width="18" height="14" viewBox="0 0 18 14"><path d="M1 7h14M10 2l5 5-5 5" fill="none" stroke="#111" stroke-width="2"/></svg></div></div>
  </div>
  <div class="abs service-card" style="left:758px">
    <div class="service-photo" role="img" aria-label="Rows of outdoor condenser units"></div>
    <div class="service-panel">Lorem ipsum dolor<div class="service-go"><svg width="18" height="14" viewBox="0 0 18 14"><path d="M1 7h14M10 2l5 5-5 5" fill="none" stroke="#111" stroke-width="2"/></svg></div></div>
  </div>
</section>

<section>
  <h2 class="abs section-title" style="top:2042px">ABOUT US</h2>
  <div class="abs section-rule" style="top:2108px"></div>
  <div class="abs about-card" style="left:110px">
    <h3>Lorem ipsum dolor<br>sit amet, consectetur adipiscing</h3>
    <p>Lorem ipsum dolor sit amet, consectetur adipiscing elit, sed do eiusmod tempor incididunt ut labore et dolore magna aliqua. Quis ipsum suspendisse ultrices gravida. Risus commodo viverra maecenas accumsan lacus vel facilisis.</p>
  </div>
  <div class="abs about-card" style="left:620px;padding-left:64px">
    <h3>Lorem ipsum dolor sit amet, consectetur adipiscing elit, sed do</h3>
    <p>Lorem ipsum dolor sit amet, consectetur adipiscing elit, sed do eiusmod tempor incididunt ut labore et dolore magna aliqua.</p>
  </div>
  <div class="abs about-badge">Pelican<br>HVAC</div>
  <div class="abs btn about-btn">READ MORE
    <svg width="16" height="16" viewBox="0 0 16 16"><circle cx="8" cy="8" r="7" fill="none" stroke="#fff" stroke-width="1.6"/><path d="M6.5 4.5 10 8l-3.5 3.5" fill="none" stroke="#fff" stroke-width="1.6"/></svg>
  </div>
</section>

<section>
  <div class="abs request" role="img" aria-label="Dark photo of an air conditioning unit"><div class="request-photo"></div></div>
  <h2 class="abs request-title">REQUEST A SERVICE CALL</h2>
  <div class="abs request-rule"></div>
  <div class="abs field" style="top:2782px">Full Name</div>
  <div class="abs field" style="top:2846px">Email Address</div>
  <div class="abs field" style="top:2910px">Phone Number</div>
  <div class="abs field field-upload" style="top:2974px">Upload A Image
    <svg width="18" height="18" viewBox="0 0 18 18"><path d="M9 12V2M4.5 6.5 9 2l4.5 4.5M2 13v3h14v-3" fill="none" stroke="#fff" stroke-width="2"/></svg>
  </div>
  <div class="abs field field-message" style="top:3030px">Message</div>
  <div class="abs btn submit">SUBMIT
    <svg width="16" height="16" viewBox="0 0 16 16"><circle cx="8" cy="8" r="7" fill="none" stroke="#fff" stroke-width="1.6"/><path d="M6.5 4.5 10 8l-3.5 3.5" fill="none" stroke="#fff" stroke-width="1.6"/></svg>
  </div>
</section>

<footer>
  <div class="abs footer-brand"><span class="brand-dot" style="width:24px;height:24px"></span><span class="brand-name">Pelican HVAC</span></div>
  <nav class="abs footer-nav"><span>HOME</span><span>ABOUT</span><span>SERVICES</span><span>CONTACT US</span></nav>
  <div class="abs footer-rule"></div>
  <div class="abs copyright">Copyright 2024 PELICAN HVAC</div>
  <div class="abs legal"><span>SITEMAP</span><span>|</span><span>TERMS</span><span>|</span><span>COOKIES</span><span>|</span><span>LEGAL</span></div>
</footer>

</body>
</html>
```